Brightwave Reach - Business Card

We need a business card for a Social Media Marketing company that specializes in online marketing for small businesses in Canada using common Social Media platforms such as Pixlora, Chatterly, Blinkpost & Quibber.

I have uploaded a copy of our logo which I would like utilized in the business card. We would like the business card to be modern yet classy design.

Our website is www.brightwavereach.ca

Industry/Entity Type

Marketing

Contact Information for Business Card

Email: info@brightwavereach.ca
Website: www.brightwavereach.ca
Telephone: 604-555-0193

Colors

Designer to choose colors to be used in the design.

Requirements
Must have
• Social Media icons on reverse
• Please add some designs with color.

```html
<!DOCTYPE html>
<html lang="en">
<head>
<meta charset="utf-8">
<title>Brightwave Reach – Business Card</title>
<link href="https://fonts.googleapis.com/css2?family=Lato:wght@400;700;900&display=swap" rel="stylesheet">
<style>
  :root{
    --bg:#e6e6e6;
    --paper:#ffffff;
    --ink:#111111;
    --slate:#4a4d50;
    --logo:#3b3b3b;
    --soft:#f0f0f0;
    --text:#2a2a2a;
    --tag:#ffffff;
  }
  *{box-sizing:border-box;margin:0;padding:0}
  html,body{width:1200px;height:880px;overflow:hidden;background:var(--bg);font-family:"Lato",sans-serif}
  .canvas{position:relative;width:1200px;height:880px}
  .card{position:absolute;width:640px;height:366px;background:var(--paper);overflow:hidden;box-shadow:0 10px 30px rgba(0,0,0,.18)}
  .card--front{left:140px;top:50px}
  .card--back{left:420px;top:464px}
  .band{position:absolute}
  .band--black{background:var(--ink)}
  .band--slate{background:var(--slate)}
  .soft-glow{position:absolute;border-radius:50%;background:radial-gradient(ellipse at center,var(--soft) 0%,rgba(255,255,255,0) 70%)}
  .logo{position:absolute;display:flex;align-items:center;justify-content:center;gap:8px}
  .logo__mark{width:14px;height:14px;background:var(--logo);flex:none}
  .logo__name{font-weight:900;color:var(--logo);text-transform:uppercase;line-height:1;letter-spacing:.5px;white-space:nowrap}
  .front-web{position:absolute;left:200px;width:230px;top:292px;text-align:center;font-size:15px;letter-spacing:1.5px;color:var(--text)}
  .tagline{position:absolute;display:flex;align-items:center;justify-content:center;text-align:center;color:var(--tag);font-weight:900;font-size:15px;line-height:1.25;letter-spacing:.5px;text-transform:uppercase}
  .person{position:absolute;left:420px;top:188px;font-weight:900;font-size:20px;color:var(--ink);text-transform:uppercase}
  .contacts{position:absolute;left:420px;top:226px;list-style:none}
  .contacts li{display:flex;align-items:center;gap:8px;height:24px;font-size:15px;color:var(--text)}
  .contacts svg{width:18px;height:18px;flex:none}
  .socials{position:absolute;left:40px;top:318px;display:flex;gap:16px;list-style:none}
  .socials li{display:flex;align-items:center;gap:5px;font-size:11px;font-weight:700;color:var(--ink)}
  .socials .sq{width:16px;height:16px;background:var(--ink)}
</style>
</head>
<body>
<main class="canvas">

  <section class="card card--front" aria-label="Card front">
    <div class="soft-glow" style="left:170px;top:10px;width:320px;height:346px"></div>
    <div class="band band--black" style="left:0;top:150px;width:200px;height:28px"></div>
    <div class="band band--slate" style="left:0;top:178px;width:200px;height:100px"></div>
    <div class="band band--black" style="left:430px;top:52px;width:210px;height:28px"></div>
    <div class="band band--slate" style="left:430px;top:80px;width:210px;height:96px"></div>
    <div class="logo" style="left:200px;top:150px;width:230px;height:60px">
      <span class="logo__mark"></span>
      <span class="logo__name" style="font-size:24px">Brightwave Reach</span>
    </div>
    <p class="front-web">www.brightwavereach.ca</p>
  </section>

  <section class="card card--back" aria-label="Card back">
    <div class="soft-glow" style="left:380px;top:120px;width:280px;height:260px"></div>
    <div class="band band--black" style="left:0;top:112px;width:110px;height:30px"></div>
    <div class="band band--slate" style="left:0;top:142px;width:110px;height:92px"></div>
    <div class="logo" style="left:118px;top:140px;width:180px;height:50px">
      <span class="logo__mark" style="width:12px;height:12px"></span>
      <span class="logo__name" style="font-size:17px">Brightwave Reach</span>
    </div>
    <div class="band band--black" style="left:300px;top:28px;width:340px;height:32px"></div>
    <div class="band band--slate tagline" style="left:330px;top:60px;width:310px;height:100px">Connecting your business,<br>with your community</div>
    <p class="person">Daniel Brooks</p>
    <ul class="contacts">
      <li><svg viewBox="0 0 18 18"><rect width="18" height="18" fill="#111"/><path d="M5 4h3l1 3-2 1c1 2 2 3 3 3l1-2 3 1v3c-6 0-9-3-9-9z" fill="#fff"/></svg>604-555-0193</li>
      <li><svg viewBox="0 0 18 18"><rect width="18" height="18" fill="#111"/><rect x="3.5" y="5" width="11" height="8" fill="none" stroke="#fff" stroke-width="1.3"/><path d="M3.5 5l5.5 4.5L14.5 5" fill="none" stroke="#fff" stroke-width="1.3"/></svg>info@brightwavereach.ca</li>
      <li><svg viewBox="0 0 18 18"><rect width="18" height="18" fill="#111"/><circle cx="9" cy="9" r="5" fill="none" stroke="#fff" stroke-width="1.2"/><ellipse cx="9" cy="9" rx="2" ry="5" fill="none" stroke="#fff" stroke-width="1"/><path d="M4 9h10" stroke="#fff" stroke-width="1"/></svg>www.brightwavereach.ca</li>
    </ul>
    <ul class="socials">
      <li><span class="sq"></span>Chatterly</li>
      <li><span class="sq"></span>Quibber</li>
      <li><span class="sq"></span>Pixlora</li>
      <li><span class="sq"></span>Blinkpost</li>
    </ul>
  </section>

</main>
</body>
</html>
```